2 Flow Charts showing Fair Trade vs Market Trade****See new image*****

I am starting a coffee roasting company where I warehouse coffee for farmers I met in Nicaragua as a Harbor League Volunteer.

I need one flow chart to show the normal path of coffee, from the producer to the exporter, to the importer, to the roaster, and ultimately to the consumer, each of which taking a little along the way, leaving the farmer less.

Then another flow chart showing a close relationship between my company (Brass Lantern Coffee) and the producer, with out the exporter/importer, and more money going to the farmer.

I have included my attempt at the flow charts, which look clunky and are in super low res.

You can see how I want to use the flow charts in the following website:

brasslanterncoffeeroasters.example

****** Just reduced the verbiage on the Flow Charts****************
***************See new image*******************************

Target Market(s)

Coffee consumers interested in fair trade.

Industry/Entity Type

It Company

Font styles to use
Sans Serif

Requirements
Must have
• Originally thinking black and white, but am open to color.
Nice to have
• Would like to see a design in both color and monochrome. I am having a difficult time determining which would look better on the site.

```html
<!DOCTYPE html>
<html lang="en">
<head>
<meta charset="utf-8">
<title>The Brass Lantern Model</title>
<link href="https://fonts.googleapis.com/css2?family=Jost:wght@400;500;600;700;800&display=swap" rel="stylesheet">
<style>
  :root {
    --blue: #3a87d0;
    --orange: #f15a2b;
    --blush: #f7c2b3;
    --roast: #6b4a3a;
    --black: #000;
    --grey: #8a8a8a;
    --pale-grey: #bdbdbd;
    --paper: #fff;
  }
  html, body { margin: 0; padding: 0; overflow: hidden; background: var(--paper); }
  .canvas { position: relative; width: 1200px; height: 1000px; overflow: hidden; background: var(--paper); font-family: "Jost", sans-serif; }
  .model { position: absolute; left: 0; width: 1200px; height: 496px; display: block; }
  .model--colour { top: 0; --title: var(--blue); --accent: var(--blue); --key: var(--orange); --ring: var(--orange); --ring-num: var(--blue); --middle: var(--blue); --money: var(--blush); --brand: var(--orange); --bracket: var(--orange); --bean: var(--roast); --placeholder: #9dc3ea; --end-ring: var(--orange); --end-num: var(--blue); }
  .model--mono { top: 496px; --title: var(--black); --accent: var(--black); --key: var(--black); --ring: var(--grey); --ring-num: var(--grey); --middle: var(--grey); --money: var(--pale-grey); --brand: var(--black); --bracket: var(--black); --bean: var(--black); --placeholder: #b5b5b5; --end-ring: var(--black); --end-num: var(--black); }
  .divider { position: absolute; left: 0; top: 493px; width: 1200px; height: 7px; background: var(--black); }

  .title { font-family: "Jost", sans-serif; font-weight: 700; font-size: 40px; fill: var(--title); letter-spacing: 0.3px; }
  .tagline { font-family: "Jost", sans-serif; font-weight: 600; font-size: 16px; fill: var(--accent); }
  .bracket { fill: none; stroke: var(--bracket); stroke-width: 2.5; }
  .tab-box { fill: var(--accent); }
  .tab-text { font-family: "Jost", sans-serif; font-weight: 700; font-size: 16px; fill: var(--paper); letter-spacing: 0.3px; }
  .stage-label { font-family: "Jost", sans-serif; font-weight: 700; fill: var(--accent); }
  .middle-label { font-family: "Jost", sans-serif; font-weight: 700; font-size: 11px; fill: var(--middle); }
  .money { font-family: "Jost", sans-serif; font-weight: 600; font-size: 15px; fill: var(--money); }
  .money-line { fill: none; stroke: var(--money); stroke-width: 2; }
  .path-line { fill: none; stroke: var(--accent); stroke-width: 2.2; }
  .icon-middle { fill: none; stroke: var(--middle); stroke-width: 2.4; stroke-linejoin: round; }
  .node-key { fill: var(--key); }
  .node-ring { fill: var(--paper); stroke: var(--ring); stroke-width: 2; }
  .node-end { fill: var(--paper); stroke: var(--end-ring); stroke-width: 2; }
  .node-key-num { font-family: "Jost", sans-serif; font-weight: 700; font-size: 11px; fill: var(--paper); }
  .node-ring-num { font-family: "Jost", sans-serif; font-weight: 700; font-size: 11px; fill: var(--ring-num); }
  .node-end-num { font-family: "Jost", sans-serif; font-weight: 700; font-size: 11px; fill: var(--end-num); }
  .note { font-family: "Jost", sans-serif; font-weight: 500; font-size: 13px; fill: var(--accent); }
  .note-strong { font-family: "Jost", sans-serif; font-weight: 700; font-size: 13px; fill: var(--accent); }
  .cup { fill: none; stroke: var(--accent); stroke-width: 3.5; stroke-linecap: round; }
  .cup-bean { fill: var(--bean); }
  .steam { fill: none; stroke: var(--accent); stroke-width: 2; stroke-linecap: round; }
  .steam--brand { stroke: var(--brand); }
  .brand-mark { fill: var(--brand); }
  .brand-label { font-family: "Jost", sans-serif; font-weight: 700; font-size: 19px; fill: var(--brand); }
  .brand-sub { font-family: "Jost", sans-serif; font-weight: 400; font-size: 13px; fill: var(--brand); }
  .dollar { font-family: "Jost", sans-serif; font-weight: 800; font-size: 22px; fill: var(--accent); stroke: var(--paper); stroke-width: 6px; paint-order: stroke; }
  .arrow-line { fill: none; stroke: var(--accent); stroke-width: 2.2; }
  .placeholder { fill: var(--placeholder); }
  .bean-ring { fill: var(--paper); stroke: var(--brand); stroke-width: 2.2; }
</style>
</head>
<body>
<div class="canvas">
  <svg width="0" height="0" style="position:absolute" aria-hidden="true">
    <defs>
      <symbol id="bean" viewBox="-7 -5 14 10">
        <ellipse cx="0" cy="0" rx="6.5" ry="4.2" transform="rotate(-25)" fill="var(--bean)"/>
        <path d="M-5 2 Q0 -1 5 -2" fill="none" stroke="#fff" stroke-width="1.1" transform="rotate(-25)"/>
      </symbol>
    </defs>
  </svg>

  <svg class="model model--colour" viewBox="0 0 1200 496" role="group" aria-label="The Brass Lantern Model in colour">
    <text class="title" x="600" y="90" text-anchor="middle">THE BRASS LANTERN MODEL</text>
    <path class="bracket" d="M266 104 H259 V133 H266"/>
    <path class="bracket" d="M934 104 H941 V133 H934"/>
    <text class="tagline" x="600" y="124" text-anchor="middle">We do things differently. We do away with the middlemen and give more to the farmers.</text>

    <g class="traditional">
      <rect class="tab-box" x="258" y="157" width="182" height="26"/>
      <text class="tab-text" x="349" y="176" text-anchor="middle">TRADITIONAL TRADE</text>

      <rect class="placeholder" x="110" y="178" width="88" height="52" role="img" aria-label="Coffee tree and farmer illustration"/>
      <text class="stage-label" x="113" y="244" font-size="15">PRODUCER</text>

      <text class="money" x="198" y="221">←$</text>
      <text class="money" x="276" y="257">←$$</text>
      <text class="money" x="358" y="294">←$$$</text>
      <text class="money" x="440" y="334">←$$$$</text>
      <path class="money-line" d="M496 329 H527 V356"/>

      <path class="icon-middle" d="M232 270 V254 A17 17 0 0 1 266 254 V270 Z M228 248 A18 18 0 0 1 262 240 M236 264 H262 M236 258 H262"/>
      <text class="middle-label" x="248" y="284" text-anchor="middle">EXPORTER</text>
      <path class="icon-middle" d="M312 300 V281 L326 269 L340 281 V300 H330 V289 H322 V300 Z"/>
      <text class="middle-label" x="326" y="319" text-anchor="middle">IMPORTER</text>
      <path class="icon-middle" d="M393 340 V322 L411 306 L429 322 V340 Z M399 340 V325 L411 314 L423 325 V340"/>
      <text class="middle-label" x="411" y="359" text-anchor="middle">COFFEE ROASTER</text>

      <path class="path-line" d="M156 271 V300 H232 M241 310 V338 H315 M323 346 V378 H401 M410 386 V410 H472"/>
      <use href="#bean" x="191" y="295" width="14" height="10"/>
      <use href="#bean" x="273" y="333" width="14" height="10"/>
      <use href="#bean" x="358" y="373" width="14" height="10"/>
      <use href="#bean" x="438" y="405" width="14" height="10"/>

      <circle class="node-key" cx="156" cy="263" r="8.5"/><text class="node-key-num" x="156" y="267" text-anchor="middle">1</text>
      <circle class="node-ring" cx="241" cy="302" r="8"/><text class="node-ring-num" x="241" y="306" text-anchor="middle">2</text>
      <circle class="node-ring" cx="323" cy="338" r="8"/><text class="node-ring-num" x="323" y="342" text-anchor="middle">3</text>
      <circle class="node-ring" cx="410" cy="378" r="8"/><text class="node-ring-num" x="410" y="382" text-anchor="middle">4</text>
      <circle class="node-key" cx="481" cy="410" r="8.5"/><text class="node-key-num" x="481" y="414" text-anchor="middle">5</text>

      <path class="steam" d="M527 372 q-3 -3 0 -6 q3 -3 0 -6 M534 372 q-3 -3 0 -6 q3 -3 0 -6"/>
      <path class="cup" d="M512 378 H552 V393 A18 17 0 0 1 512 393 Z M552 382 H557 A6 6 0 0 1 557 395 H551"/>
      <ellipse class="cup-bean" cx="531" cy="392" rx="6" ry="9" transform="rotate(20 531 392)"/>
      <text class="stage-label" x="529" y="436" font-size="17" text-anchor="middle">YOUR COFFEE</text>

      <text class="note" x="114" y="419">Traditionally, farmers sell their coffee for</text>
      <text class="note-strong" x="114" y="437">1$ to $1.85 a pound</text>
    </g>

    <g class="direct">
      <rect class="tab-box" x="772" y="157" width="224" height="26"/>
      <text class="tab-text" x="884" y="176" text-anchor="middle">BRASS LANTERN TRADE</text>

      <rect class="placeholder" x="727" y="198" width="62" height="50" role="img" aria-label="Coffee tree and farmer illustration"/>
      <text class="stage-label" x="758" y="263" font-size="11" text-anchor="middle">PRODUCER</text>
      <rect class="brand-mark" x="986" y="205" width="40" height="40"/>
      <text class="stage-label" x="1006" y="263" font-size="11" text-anchor="middle">BRASS LANTERN</text>

      <text class="note" x="882" y="227" font-size="12" text-anchor="middle">We directly</text>
      <text class="note" x="882" y="242" font-size="12" text-anchor="middle">import &amp; roast</text>
      <text class="note" x="882" y="257" font-size="12" text-anchor="middle">the coffee</text>

      <path class="path-line" d="M768 276 H870 M894 276 H999"/>
      <circle class="bean-ring" cx="882" cy="276" r="12"/>
      <use href="#bean" x="874" y="270" width="16" height="12"/>

      <path class="arrow-line" d="M876 370 L766 292 M888 370 L1000 292"/>
      <path class="arrow-line" d="M764 302 L764 290 L776 290"/>
      <path class="arrow-line" d="M990 290 L1002 290 L1002 302"/>
      <text class="dollar" x="815" y="336" text-anchor="middle" transform="rotate(35 815 329)">$$</text>
      <text class="dollar" x="950" y="336" text-anchor="middle" transform="rotate(-35 950 329)">$$</text>

      <circle class="node-end" cx="760" cy="276" r="8"/><text class="node-end-num" x="760" y="280" text-anchor="middle">1</text>
      <circle class="node-end" cx="1007" cy="276" r="8"/><text class="node-end-num" x="1007" y="280" text-anchor="middle">2</text>

      <path class="steam steam--brand" d="M877 327 q-4 -4 0 -8 q4 -4 0 -8 M885 327 q-4 -4 0 -8 q4 -4 0 -8"/>
      <path class="cup" d="M862 334 H902 V348 A18 16 0 0 1 862 348 Z M902 338 H907 A6 6 0 0 1 907 351 H901"/>
      <rect class="brand-mark" x="876" y="339" width="12" height="11"/>
      <circle class="node-key" cx="882" cy="376" r="8.5"/><text class="node-key-num" x="882" y="380" text-anchor="middle">3</text>
      <text class="brand-label" x="882" y="402" text-anchor="middle">YOUR COFFEE</text>
      <text class="brand-sub" x="882" y="417" text-anchor="middle">FROM BRASS LANTERN</text>

      <text class="note" x="1101" y="387" font-size="12" text-anchor="end">We share revenues,</text>
      <text class="note" x="1101" y="402" font-size="12" text-anchor="end">guaranteeing our farmers</text>
      <text class="note-strong" x="1101" y="418" font-size="12" text-anchor="end">$3.25 a pound</text>
    </g>
  </svg>

  <div class="divider"></div>

  <svg class="model model--mono" viewBox="0 0 1200 496" role="group" aria-label="The Brass Lantern Model in black and white">
    <text class="title" x="600" y="90" text-anchor="middle">THE BRASS LANTERN MODEL</text>
    <path class="bracket" d="M266 104 H259 V133 H266"/>
    <path class="bracket" d="M934 104 H941 V133 H934"/>
    <text class="tagline" x="600" y="124" text-anchor="middle">We do things differently. We do away with the middlemen and give more to the farmers.</text>

    <g class="traditional">
      <rect class="tab-box" x="258" y="157" width="182" height="26"/>
      <text class="tab-text" x="349" y="176" text-anchor="middle">TRADITIONAL TRADE</text>

      <rect class="placeholder" x="110" y="178" width="88" height="52" role="img" aria-label="Coffee tree and farmer illustration"/>
      <text class="stage-label" x="113" y="244" font-size="15">PRODUCER</text>

      <text class="money" x="198" y="221">←$</text>
      <text class="money" x="276" y="257">←$$</text>
      <text class="money" x="358" y="294">←$$$</text>
      <text class="money" x="440" y="334">←$$$$</text>
      <path class="money-line" d="M496 329 H527 V356"/>

      <path class="icon-middle" d="M232 270 V254 A17 17 0 0 1 266 254 V270 Z M228 248 A18 18 0 0 1 262 240 M236 264 H262 M236 258 H262"/>
      <text class="middle-label" x="248" y="284" text-anchor="middle">EXPORTER</text>
      <path class="icon-middle" d="M312 300 V281 L326 269 L340 281 V300 H330 V289 H322 V300 Z"/>
      <text class="middle-label" x="326" y="319" text-anchor="middle">IMPORTER</text>
      <path class="icon-middle" d="M393 340 V322 L411 306 L429 322 V340 Z M399 340 V325 L411 314 L423 325 V340"/>
      <text class="middle-label" x="411" y="359" text-anchor="middle">COFFEE ROASTER</text>

      <path class="path-line" d="M156 271 V300 H232 M241 310 V338 H315 M323 346 V378 H401 M410 386 V410 H472"/>
      <use href="#bean" x="191" y="295" width="14" height="10"/>
      <use href="#bean" x="273" y="333" width="14" height="10"/>
      <use href="#bean" x="358" y="373" width="14" height="10"/>
      <use href="#bean" x="438" y="405" width="14" height="10"/>

      <circle class="node-key" cx="156" cy="263" r="8.5"/><text class="node-key-num" x="156" y="267" text-anchor="middle">1</text>
      <circle class="node-ring" cx="241" cy="302" r="8"/><text class="node-ring-num" x="241" y="306" text-anchor="middle">2</text>
      <circle class="node-ring" cx="323" cy="338" r="8"/><text class="node-ring-num" x="323" y="342" text-anchor="middle">3</text>
      <circle class="node-ring" cx="410" cy="378" r="8"/><text class="node-ring-num" x="410" y="382" text-anchor="middle">4</text>
      <circle class="node-key" cx="481" cy="410" r="8.5"/><text class="node-key-num" x="481" y="414" text-anchor="middle">5</text>

      <path class="steam" d="M527 372 q-3 -3 0 -6 q3 -3 0 -6 M534 372 q-3 -3 0 -6 q3 -3 0 -6"/>
      <path class="cup" d="M512 378 H552 V393 A18 17 0 0 1 512 393 Z M552 382 H557 A6 6 0 0 1 557 395 H551"/>
      <ellipse class="cup-bean" cx="531" cy="392" rx="6" ry="9" transform="rotate(20 531 392)"/>
      <text class="stage-label" x="529" y="436" font-size="17" text-anchor="middle">YOUR COFFEE</text>

      <text class="note" x="114" y="419">Traditionally, farmers sell their coffee for</text>
      <text class="note-strong" x="114" y="437">1$ to $1.85 a pound</text>
    </g>

    <g class="direct">
      <rect class="tab-box" x="772" y="157" width="224" height="26"/>
      <text class="tab-text" x="884" y="176" text-anchor="middle">BRASS LANTERN TRADE</text>

      <rect class="placeholder" x="727" y="198" width="62" height="50" role="img" aria-label="Coffee tree and farmer illustration"/>
      <text class="stage-label" x="758" y="263" font-size="11" text-anchor="middle">PRODUCER</text>
      <rect class="brand-mark" x="986" y="205" width="40" height="40"/>
      <text class="stage-label" x="1006" y="263" font-size="11" text-anchor="middle">BRASS LANTERN</text>

      <text class="note" x="882" y="227" font-size="12" text-anchor="middle">We directly</text>
      <text class="note" x="882" y="242" font-size="12" text-anchor="middle">import &amp; roast</text>
      <text class="note" x="882" y="257" font-size="12" text-anchor="middle">the coffee</text>

      <path class="path-line" d="M768 276 H870 M894 276 H999"/>
      <circle class="bean-ring" cx="882" cy="276" r="12"/>
      <use href="#bean" x="874" y="270" width="16" height="12"/>

      <path class="arrow-line" d="M876 370 L766 292 M888 370 L1000 292"/>
      <path class="arrow-line" d="M764 302 L764 290 L776 290"/>
      <path class="arrow-line" d="M990 290 L1002 290 L1002 302"/>
      <text class="dollar" x="815" y="336" text-anchor="middle" transform="rotate(35 815 329)">$$</text>
      <text class="dollar" x="950" y="336" text-anchor="middle" transform="rotate(-35 950 329)">$$</text>

      <circle class="node-end" cx="760" cy="276" r="8"/><text class="node-end-num" x="760" y="280" text-anchor="middle">1</text>
      <circle class="node-end" cx="1007" cy="276" r="8"/><text class="node-end-num" x="1007" y="280" text-anchor="middle">2</text>

      <path class="steam steam--brand" d="M877 327 q-4 -4 0 -8 q4 -4 0 -8 M885 327 q-4 -4 0 -8 q4 -4 0 -8"/>
      <path class="cup" d="M862 334 H902 V348 A18 16 0 0 1 862 348 Z M902 338 H907 A6 6 0 0 1 907 351 H901"/>
      <rect class="brand-mark" x="876" y="339" width="12" height="11"/>
      <circle class="node-key" cx="882" cy="376" r="8.5"/><text class="node-key-num" x="882" y="380" text-anchor="middle">3</text>
      <text class="brand-label" x="882" y="402" text-anchor="middle">YOUR COFFEE</text>
      <text class="brand-sub" x="882" y="417" text-anchor="middle">FROM BRASS LANTERN</text>

      <text class="note" x="1101" y="387" font-size="12" text-anchor="end">We share revenues,</text>
      <text class="note" x="1101" y="402" font-size="12" text-anchor="end">guaranteeing our farmers</text>
      <text class="note-strong" x="1101" y="418" font-size="12" text-anchor="end">$3.25 a pound</text>
    </g>
  </svg>
</div>
</body>
</html>
```